Luxury Business Card Design for High-End Window Treatments

Gilded Slatworks
Custom Plantation Shutters & Architectural Shading Systems

⸻

BACK

Daniel Trevick
Owner

Custom Interior & Exterior Window Treatments

919-555-0148
gildedslatworks.com

I have included a picture that I’m hoping we can use on the back, but I’m also wondering if you can get rid of the ladder? Should we get rid of shutters , shades and blinds underneath Gilded Slatworks?

Target Market(s)

High-end residential homeowners, custom home builders, architects, interior designers, and luxury renovation clients seeking premium plantation shutters and motorized architectural shading systems.

Industry/Entity Type

Custom Window treatments

Contact Information for Business Card

Front Gilded Slatworks Custom Plantation Shutters Motorized Architectural Shading Systems BACK Daniel Trevick Owner 919-555-0148 GildedSlatworks.com Custom Interior & Exterior Window Treatments By Appointment

Requirements
Nice to have
• Not 100% sure on nice to halves or the color but you can definitely check out my website to get a better understanding of what I’m trying to do

```html
<!DOCTYPE html>
<html lang="en">
<head>
<meta charset="utf-8">
<title>Gilded Slatworks – Business Cards</title>
<link rel="stylesheet" href="https://fonts.googleapis.com/css2?family=Poppins:wght@400&family=Gloock&display=swap">
<style>
  :root {
    --stage: #9a9a9a;
    --card-black: #000000;
    --gold: #c2ab4c;
    --white: #ffffff;
    --photo-sky: #8fb4d8;
    --photo-house: #4a4e55;
    --photo-green: #3d4a2e;
  }
  * { margin: 0; padding: 0; box-sizing: border-box; }
  html, body {
    width: 1093px; height: 1200px; overflow: hidden;
    background: var(--stage);
    font-family: "Poppins", sans-serif;
  }
  .canvas { position: relative; width: 1093px; height: 1200px; }

  .card {
    position: absolute; left: 264px; width: 581px;
    background: var(--card-black); overflow: hidden;
  }

  /* Contact side */
  .card--contact { top: 226px; height: 357px; }
  .name-marker {
    position: absolute; left: 0; top: 273px; margin-top: -226px;
    width: 18px; height: 34px; background: var(--gold);
  }
  .person-name {
    position: absolute; left: 26px; top: 40px;
    font-family: "Gloock", serif; font-weight: 400;
    font-size: 25px; line-height: 1; color: var(--gold);
  }
  .person-role {
    position: absolute; left: 27px; top: 67px;
    font-size: 16px; line-height: 1; color: var(--white);
  }
  .contact-list { position: absolute; left: 28px; top: 141px; list-style: none; }
  .contact-item {
    display: flex; align-items: center; gap: 8px;
    font-size: 17.5px; line-height: 21px; color: var(--white);
  }
  .contact-item svg { width: 16px; height: 16px; flex: none; }
  .service-lines {
    position: absolute; left: 27px; top: 240px;
    font-size: 17px; line-height: 21px; color: var(--gold);
  }
  .divider-band {
    position: absolute; left: 291px; top: 0; width: 22px; height: 100%;
    background: var(--gold);
  }
  .project-photo {
    position: absolute; left: 313px; top: 0; right: 0; height: 100%;
    background: linear-gradient(180deg, var(--photo-sky) 0%, #d8d3c8 16%, var(--photo-house) 26%, var(--photo-house) 62%, #6c6a66 74%, var(--photo-green) 86%, #2f3a24 100%);
  }

  /* Brand side */
  .card--brand { top: 620px; height: 359px; }
  .brand-name {
    position: absolute; left: 0; right: 0; top: 95px; text-align: center;
    font-family: "Gloock", serif; font-weight: 400;
    font-size: 62px; line-height: 70px; color: var(--gold);
  }
  .tagline-band {
    position: absolute; left: 0; right: 0; top: 276px; height: 50px;
    background: var(--gold); color: var(--white);
    text-align: center; font-size: 17px; line-height: 21px; padding-top: 4px;
  }
</style>
</head>
<body>
<main class="canvas">

  <section class="card card--contact">
    <div class="name-marker" style="top:47px;margin-top:0"></div>
    <h1 class="person-name">Daniel Trevick</h1>
    <p class="person-role">Owner</p>
    <ul class="contact-list">
      <li class="contact-item">
        <svg viewBox="0 0 24 24" aria-hidden="true"><path fill="var(--gold)" d="M6.6 10.8a15.1 15.1 0 0 0 6.6 6.6l2.2-2.2a1 1 0 0 1 1-.25 11.4 11.4 0 0 0 3.6.57 1 1 0 0 1 1 1V20a1 1 0 0 1-1 1A17 17 0 0 1 3 4a1 1 0 0 1 1-1h3.5a1 1 0 0 1 1 1c0 1.25.2 2.45.57 3.57a1 1 0 0 1-.25 1z"/></svg>
        919-555-0148
      </li>
      <li class="contact-item">
        <svg viewBox="0 0 24 24" aria-hidden="true"><path fill="var(--gold)" d="M2 5h20v14H2z"/><path fill="none" stroke="var(--card-black)" stroke-width="1.6" d="M2 5l10 8 10-8M2 19l7.5-7M22 19l-7.5-7"/></svg>
        GildedSlatworks.com
      </li>
    </ul>
    <p class="service-lines">Custom Interior &amp; Exterior<br>Window Treatments<br>By Appointment</p>
    <div class="divider-band"></div>
    <div class="project-photo" role="img" aria-label="Photo of a two-storey porch fitted with dark exterior shading screens, white columns and shrubs in front"></div>
  </section>

  <section class="card card--brand">
    <p class="brand-name">Gilded<br>Slatworks</p>
    <p class="tagline-band">Gilded Slatworks Custom | Plantation Shutters Motorized<br>Architectural Shading Systems</p>
  </section>

</main>
</body>
</html>
```